Halberd Guard Services

Our Company is a security business which needs a cut edge design, the final product should have all relevant information and maintain a bold but modern and professional look.

Target Market(s)

A cut edge design which will attract any audience

Industry/Entity Type

Security

Contact Information for Business Card

HALBERD GUARD SERVICES

Gregor Lindqvist
Operations Manager
Phone: 0491 735 219

Email: info@halberdguard.com.au
Web: www.halberdguard.com.au

Requirements
Must have
• Must be double sided and contain all relevant information and the company logo.

```html
<!DOCTYPE html>
<html lang="en">
<head>
<meta charset="utf-8">
<title>Halberd Guard Services – Business Card</title>
<link rel="stylesheet" href="https://fonts.googleapis.com/css2?family=Open+Sans:wght@400;600;800&display=swap">
<style>
  :root {
    --bg: #e6e7e9;
    --card: #ffffff;
    --card-shade: #e9eaec;
    --brand-dark: #3e5c64;
    --teal: #4e6f78;
    --teal-deep: #45646d;
    --orange: #f2a53a;
    --orange-deep: #e8922a;
    --ink: #2b2b2b;
    --white: #ffffff;
  }
  * { margin: 0; padding: 0; box-sizing: border-box; }
  html, body { width: 1200px; height: 951px; overflow: hidden; }
  body {
    background: var(--bg);
    font-family: "Open Sans", Verdana, sans-serif;
    position: relative;
  }
  .card {
    position: absolute;
    width: 580px;
    height: 330px;
    border-radius: 22px;
    background: var(--card);
    box-shadow: 0 10px 28px rgba(0,0,0,.18);
    overflow: hidden;
  }
  /* Front side */
  .card--front { left: 110px; top: 100px; }
  .brand {
    position: absolute;
    left: 0; right: 0; top: 110px;
    display: flex; align-items: center; justify-content: center; gap: 16px;
  }
  .brand__mark {
    width: 34px; height: 34px;
    background: var(--brand-dark);
  }
  .brand__name {
    font-weight: 800;
    font-size: 46px;
    letter-spacing: 1px;
    color: var(--brand-dark);
    white-space: nowrap;
  }
  .front__web {
    position: absolute;
    left: 0; right: 0; bottom: 56px;
    text-align: center;
    font-size: 19px;
    font-weight: 600;
    letter-spacing: 1px;
    color: var(--ink);
  }
  /* Back side */
  .card--back {
    left: 510px; top: 520px;
    background: linear-gradient(180deg, var(--card) 0%, var(--card-shade) 30%, var(--card) 55%, var(--card-shade) 100%);
  }
  .band {
    position: absolute;
    left: 0; right: 0; top: 96px; height: 152px;
    display: flex;
  }
  .band__person {
    width: 215px;
    background: linear-gradient(180deg, var(--orange) 0%, var(--orange-deep) 100%);
    color: var(--white);
    padding: 0 0 0 30px;
    display: flex; flex-direction: column; justify-content: center;
    white-space: nowrap;
  }
  .person__name { font-size: 20px; font-weight: 400; line-height: 1.15; }
  .person__role { font-size: 13px; font-weight: 600; margin-top: 2px; }
  .band__contact {
    flex: 1;
    background: linear-gradient(180deg, var(--teal) 0%, var(--teal-deep) 100%);
    color: var(--white);
    position: relative;
    padding: 0 0 0 48px;
    display: flex; flex-direction: column; justify-content: center;
    font-size: 15px;
    line-height: 1.45;
    letter-spacing: .3px;
    white-space: nowrap;
  }
  .band__divider {
    position: absolute;
    left: 22px; top: 46px;
    width: 2px; height: 34px;
    background: var(--white);
  }
</style>
</head>
<body>
  <section class="card card--front" aria-label="Business card front">
    <div class="brand">
      <span class="brand__mark"></span>
      <span class="brand__name">HALBERD GUARD</span>
    </div>
    <p class="front__web">www.halberdguard.com.au</p>
  </section>

  <section class="card card--back" aria-label="Business card back">
    <div class="band">
      <div class="band__person">
        <p class="person__name">Gregor Lindqvist</p>
        <p class="person__role">Operations Manager</p>
      </div>
      <div class="band__contact">
        <span class="band__divider"></span>
        <p>ph. 0491 735 219</p>
        <p>info@halberdguard.com.au</p>
        <p>www.halberdguard.com.au</p>
      </div>
    </div>
  </section>
</body>
</html>
```